Business Card Design Project

We are a construction company in Orange County, CA. We need a two sided business card. We would like the back to be our logo with web URL. Front should included Name, title, address, phone, fax and email address.

our address is
627 West Dorrance Blvd, Suite 308
Anaheim, CA 92718

Our logo files are attached.

Construction

```html
<!DOCTYPE html>
<html lang="en">
<head>
<meta charset="utf-8">
<title>Arden Business Card</title>
<link rel="stylesheet" href="https://fonts.googleapis.com/css2?family=Open+Sans:wght@400;700&display=swap">
<style>
  :root {
    --brand-blue: #1a4a7c;
    --card-white: #ffffff;
    --text-grey: #555555;
    --backdrop: #e8e6e3;
    --contact-white: #ffffff;
  }
  * { margin: 0; padding: 0; box-sizing: border-box; }
  html, body {
    width: 1200px;
    height: 444px;
    overflow: hidden;
    background: var(--backdrop);
    font-family: "Open Sans", Arial, sans-serif;
  }
  .canvas {
    position: relative;
    width: 1200px;
    height: 444px;
  }
  .card {
    position: absolute;
    top: 75px;
    width: 514px;
    height: 294px;
    background: var(--card-white);
    border-radius: 12px;
    overflow: hidden;
    box-shadow: 0 2px 6px rgba(0,0,0,0.18);
  }
  .card--front { left: 67px; }
  .card--back { left: 619px; }

  .front-bands {
    position: absolute;
    inset: 0;
    width: 100%;
    height: 100%;
  }
  .front-bands polygon { fill: var(--brand-blue); }

  .person-name {
    position: absolute;
    left: 167px;
    top: 40px;
    font-size: 17px;
    font-weight: 700;
    color: var(--contact-white);
    letter-spacing: 0.2px;
  }
  .person-title {
    position: absolute;
    left: 167px;
    top: 63px;
    font-size: 13px;
    font-weight: 400;
    color: var(--contact-white);
  }

  .wordmark {
    position: absolute;
    font-size: 60px;
    line-height: 1;
    font-weight: 700;
    color: var(--brand-blue);
    letter-spacing: -1px;
  }
  .card--front .wordmark { left: 147px; top: 99px; }
  .card--back .wordmark {
    left: 0;
    right: 0;
    top: 99px;
    text-align: center;
  }

  .address {
    position: absolute;
    left: 34px;
    top: 206px;
    font-size: 14px;
    line-height: 19px;
    color: var(--text-grey);
    font-style: normal;
  }

  .contact-list {
    position: absolute;
    left: 255px;
    top: 185px;
    list-style: none;
    color: var(--contact-white);
    font-size: 14px;
    line-height: 18px;
  }
  .contact-list li {
    display: flex;
    align-items: center;
    gap: 8px;
  }
  .contact-icon {
    width: 11px;
    height: 11px;
    flex: none;
  }
  .contact-icon * { fill: none; stroke: var(--contact-white); stroke-width: 1.6; }
  .contact-icon .solid { fill: var(--contact-white); stroke: none; }

  .back-url {
    position: absolute;
    left: 0;
    right: 0;
    top: 177px;
    text-align: center;
    font-size: 12px;
    letter-spacing: 3px;
    color: var(--text-grey);
  }
</style>
</head>
<body>
<main class="canvas">

  <section class="card card--front" aria-label="Card front">
    <svg class="front-bands" viewBox="0 0 524 299" preserveAspectRatio="none" aria-hidden="true">
      <polygon points="84,0 302,0 369,95 147,95"/>
      <polygon points="147,168 369,168 462,299 237,299"/>
    </svg>

    <p class="person-name">YOUR NAME</p>
    <p class="person-title">Title</p>

    <p class="wordmark">ARDEN</p>

    <address class="address">
      627 West Dorrance<br>
      Blvd, Suite 308<br>
      Anaheim, CA 92718
    </address>

    <ul class="contact-list">
      <li>
        <svg class="contact-icon" viewBox="0 0 12 12" aria-hidden="true"><circle cx="6" cy="6" r="5"/><path class="solid" d="M4 3.5 L5.2 3.5 L5.6 5 L4.9 5.6 Q5.6 7 6.9 7.6 L7.4 6.9 L8.6 7.3 L8.6 8.5 Q5 8.8 4 3.5Z"/></svg>
        <span>0123456789</span>
      </li>
      <li>
        <svg class="contact-icon" viewBox="0 0 12 12" aria-hidden="true"><path class="solid" d="M1 4 Q6 0 11 4 L10 5.5 L8 4.8 L8 4 Q6 3 4 4 L4 4.8 L2 5.5Z"/><rect class="solid" x="2.5" y="6.5" width="7" height="4" rx="1"/></svg>
        <span>0123456789</span>
      </li>
      <li>
        <svg class="contact-icon" viewBox="0 0 12 12" aria-hidden="true"><rect class="solid" x="1" y="3" width="10" height="7"/><path d="M1 3 L6 7 L11 3" style="stroke:var(--brand-blue);stroke-width:1"/></svg>
        <span>info@arden.com</span>
      </li>
      <li>
        <svg class="contact-icon" viewBox="0 0 12 12" aria-hidden="true"><circle cx="6" cy="6" r="5" style="stroke-width:1.2"/><ellipse cx="6" cy="6" rx="2.2" ry="5" style="stroke-width:1"/><path d="M1 6 H11" style="stroke-width:1"/></svg>
        <span>www.arden.com</span>
      </li>
    </ul>
  </section>

  <section class="card card--back" aria-label="Card back">
    <p class="wordmark">ARDEN</p>
    <p class="back-url">www.arden.com</p>
  </section>

</main>
</body>
</html>
```